q-zen design for startup inpection service

building and pest inspections what i had in mind was q-zen in large print with prepurchase in small print directly under it and the small tm (tradmark) .Within the C I would like an eye but I don't want to take away from the C so maybe the eye would be done in a fine line?I would also like the Building and Pest inspections to be prominent and large .Have no idea of colors but do like black orange and silver

Target Market(s)

home buyers and realestate agents

Industry/Entity Type

Building

Contact Information for Business Card

q-zen prepurchase, Phone 0412093816, fax 02 71934058, email q-zen@mailbrook.com.au ,building and pest inspections

Font styles to use
Sans Serif

Requirements
Must have
• bold color
• simple layout
• bold color
• uncluttered layout
Should not have
• contact details the same size as Building and Pest Inspections

```html
<!DOCTYPE html>
<html lang="en">
<head>
<meta charset="utf-8">
<title>q-zen prepurchase business card</title>
<link href="https://fonts.googleapis.com/css2?family=Exo+2:wght@400;600&display=swap" rel="stylesheet">
<style>
  :root {
    --bg: #efece6;
    --indigo: #2f2790;
    --indigo-deep: #231c73;
    --indigo-light: #4a3fb0;
    --sky: #1e8fd0;
    --ink: #2b2466;
    --paper: #ffffff;
    --paper-shade: #eceef1;
    --white: #ffffff;
  }
  * { margin: 0; padding: 0; box-sizing: border-box; }
  html, body {
    width: 1200px; height: 885px; overflow: hidden;
    background: var(--bg);
    font-family: "Exo 2", sans-serif;
  }
  .canvas { position: relative; width: 1200px; height: 885px; }
  .card {
    position: absolute; left: 240px; width: 720px; height: 400px;
    border-radius: 4px; overflow: hidden;
    box-shadow: 0 6px 18px rgba(0,0,0,.18);
  }
  .card-front {
    top: 30px;
    background: linear-gradient(125deg, var(--indigo-deep) 0%, var(--indigo) 45%, var(--indigo-light) 60%, var(--indigo) 75%, var(--indigo-deep) 100%);
  }
  .front-wordmark {
    position: absolute; right: 50px; bottom: 60px;
    color: var(--white); font-weight: 600; font-size: 46px;
    letter-spacing: 2px; text-transform: uppercase; white-space: nowrap;
  }
  .card-back {
    top: 455px;
    background: linear-gradient(135deg, var(--paper) 0%, var(--paper) 55%, var(--paper-shade) 100%);
  }
  .person { position: absolute; left: 50px; top: 150px; color: var(--ink); }
  .person-name { font-weight: 600; font-size: 24px; }
  .person-role { font-size: 15px; margin-top: 2px; }
  .brand { position: absolute; right: 50px; top: 50px; text-align: left; }
  .brand-name {
    color: var(--ink); font-weight: 600; font-size: 38px;
    text-transform: uppercase; letter-spacing: 1px; line-height: 1; white-space: nowrap;
  }
  .brand-tagline { color: var(--ink); font-size: 26px; margin-top: 10px; white-space: nowrap; }
  .contacts {
    position: absolute; left: 50px; bottom: 50px;
    padding-left: 24px; border-left: 2px solid var(--sky);
    color: var(--ink); font-size: 18px; line-height: 1.55;
  }
  .contact-row { display: flex; align-items: center; gap: 10px; }
  .contact-icon { width: 18px; height: 18px; flex: none; }
</style>
</head>
<body>
<main class="canvas">
  <section class="card card-front" aria-label="Card front">
    <div class="front-wordmark">q-zen prepurchase</div>
  </section>

  <section class="card card-back" aria-label="Card back">
    <div class="brand">
      <div class="brand-name">q-zen prepurchase</div>
      <div class="brand-tagline">building and pest inspections</div>
    </div>

    <div class="person">
      <div class="person-name">Your Name</div>
      <div class="person-role">Director</div>
    </div>

    <div class="contacts">
      <div class="contact-row">
        <svg class="contact-icon" viewBox="0 0 20 20" aria-hidden="true">
          <path d="M4 3h3l1.5 4-2 1.2a10 10 0 0 0 5.3 5.3L13 11.5l4 1.5v3a1.5 1.5 0 0 1-1.6 1.5A14 14 0 0 1 2.5 4.6 1.5 1.5 0 0 1 4 3z" fill="var(--sky)"/>
        </svg>
        <span>0412093816</span>
      </div>
      <div class="contact-row">
        <svg class="contact-icon" viewBox="0 0 20 20" aria-hidden="true">
          <rect x="5" y="2" width="10" height="6" fill="none" stroke="var(--sky)" stroke-width="1.6"/>
          <rect x="2" y="8" width="16" height="7" rx="1.5" fill="var(--sky)"/>
          <rect x="5" y="13" width="10" height="5" fill="var(--paper)" stroke="var(--sky)" stroke-width="1.6"/>
        </svg>
        <span>02 71934058</span>
      </div>
      <div class="contact-row">
        <svg class="contact-icon" viewBox="0 0 20 20" aria-hidden="true">
          <rect x="1.5" y="4" width="17" height="12" rx="1.5" fill="var(--sky)"/>
          <path d="M2.5 5l7.5 6 7.5-6" fill="none" stroke="var(--paper)" stroke-width="1.5"/>
        </svg>
        <span>q-zen@mailbrook.com.au</span>
      </div>
    </div>
  </section>
</main>
</body>
</html>
```